Business Card design for law firm = Brightvale Australia

We are seeking a new design for our business cards.
We are keeping our logo, which is attached.
We need space for
Name
Title
Address is , which is
Level 7
214 Marlowe Street
Sydney NSW 2047
Phone :
Mobile :
Fax :
Email :
DX :
website www.brightvale-example.com.au

Industry/Entity Type

Law Firm / Banking and Finance

Contact Information for Business Card

We are seeking a new design for our business cards. We are keeping our logo. We need space for Name Title Address is Level 7 214 Marlowe Street Sydney NSW 2047 Phone Mobile Fax Email DX website www.brightvale-example.com.au

Colors
0054AA
0677BA
7BADD7
CADEEF
E8F1F8

Requirements
Must have
• see our website for general feel www.brightvale-example.com.au

```html
<!DOCTYPE html>
<html lang="en">
<head>
<meta charset="utf-8">
<title>Brightvale Australia – Business Card</title>
<link rel="stylesheet" href="https://fonts.googleapis.com/css2?family=EB+Garamond:wght@400&display=swap">
<style>
  :root {
    --backdrop: #2b2b2c;
    --card-dark: #1a1b1d;
    --card-light: #2b2c2f;
    --mark-ink: #0d0e0f;
    --brand-blue: #3d57a8;
    --accent-blue: #1e90c4;
    --body-text: #e4e4e4;
  }
  * { margin: 0; padding: 0; box-sizing: border-box; }
  html, body {
    width: 1200px;
    height: 1138px;
    overflow: hidden;
    background: var(--backdrop);
  }
  .canvas {
    position: relative;
    width: 1200px;
    height: 1138px;
  }
  .card {
    position: absolute;
    left: 273px;
    width: 620px;
    height: 376px;
    border-radius: 16px;
    background: linear-gradient(160deg, var(--card-dark) 0%, #202124 55%, var(--card-light) 100%);
    overflow: hidden;
  }
  .card--front { top: 184px; }
  .card--back { top: 606px; }

  /* Front */
  .front-name {
    position: absolute;
    left: 0;
    right: 0;
    top: 160px;
    display: flex;
    justify-content: center;
    align-items: center;
    gap: 14px;
  }
  .front-name__dot {
    width: 14px;
    height: 14px;
    border-radius: 50%;
    background: var(--mark-ink);
  }
  .front-name__text {
    font-family: "EB Garamond", serif;
    font-size: 52px;
    line-height: 1;
    color: var(--mark-ink);
  }

  /* Back: firm name */
  .firm {
    position: absolute;
    left: 62px;
    top: 168px;
    display: flex;
    align-items: center;
    gap: 10px;
  }
  .firm__dot {
    width: 10px;
    height: 10px;
    border-radius: 50%;
    background: var(--brand-blue);
  }
  .firm__name {
    font-family: "EB Garamond", serif;
    font-size: 39px;
    line-height: 1;
    color: var(--brand-blue);
  }

  /* Back: contact */
  .contact {
    position: absolute;
    left: 347px;
    top: 104px;
    font-family: "EB Garamond", serif;
    color: var(--body-text);
  }
  .contact__name {
    font-size: 29px;
    line-height: 1;
    color: var(--brand-blue);
  }
  .contact__title {
    margin-top: 4px;
    font-size: 16px;
  }
  .contact__address {
    margin-top: 14px;
    font-size: 16px;
    line-height: 20px;
    font-style: normal;
  }
  .contact__lines {
    margin-top: 11px;
    list-style: none;
    font-size: 15px;
    line-height: 20px;
  }
  .contact__lines li {
    display: flex;
    align-items: center;
    gap: 13px;
    white-space: nowrap;
  }
  .contact__icon {
    width: 12px;
    height: 12px;
    flex: none;
    fill: var(--accent-blue);
  }
</style>
</head>
<body>
<div class="canvas">

  <section class="card card--front" aria-label="Card front">
    <div class="front-name">
      <span class="front-name__dot"></span>
      <span class="front-name__text">Brightvale</span>
    </div>
  </section>

  <section class="card card--back" aria-label="Card back">
    <div class="firm">
      <span class="firm__dot"></span>
      <span class="firm__name">Brightvale</span>
    </div>

    <div class="contact">
      <div class="contact__name">Sam Hartley</div>
      <div class="contact__title">Managing Director</div>
      <address class="contact__address">
        Level 7 214 Marlowe St<br>
        Sydney NSW 2047
      </address>
      <ul class="contact__lines">
        <li>
          <svg class="contact__icon" viewBox="0 0 12 12" aria-label="Phone"><path d="M1 3.5C1 2.5 3 1.5 6 1.5S11 2.5 11 3.5V5H8.5V4H3.5V5H1Z"/><path d="M3 5.5H9L10.5 10.5H1.5Z"/></svg>
          <span>02 5550 0148</span>
        </li>
        <li>
          <svg class="contact__icon" viewBox="0 0 12 12" aria-label="Fax"><rect x="3" y="1" width="6" height="3"/><rect x="1" y="4.5" width="10" height="4.5" rx="1"/><rect x="3" y="8" width="6" height="3"/></svg>
          <span>02 5550 0162</span>
        </li>
        <li>
          <svg class="contact__icon" viewBox="0 0 12 12" aria-label="Email"><path d="M1 2.5H11V9.5H1Z"/><path d="M1 2.5L6 6.5L11 2.5" fill="none" stroke="#1a1b1d" stroke-width="1"/></svg>
          <span>sam.hartley@brightvale-example.com.au</span>
        </li>
        <li>
          <svg class="contact__icon" viewBox="0 0 12 12" aria-label="Website"><circle cx="6" cy="6" r="5"/><path d="M1 6H11M6 1V11M2.2 3.5H9.8M2.2 8.5H9.8" stroke="#1a1b1d" stroke-width="0.7" fill="none"/><ellipse cx="6" cy="6" rx="2.3" ry="5" fill="none" stroke="#1a1b1d" stroke-width="0.7"/></svg>
          <span>www.brightvale-example.com.au</span>
        </li>
      </ul>
    </div>
  </section>

</div>
</body>
</html>
```